Candle Rental Business seeks new website design

We need a new website design for a Candle hire business. The business rents out pillar candles for events such as weddings and corporate events. Our main target market is weddings. The business name is Hire a Lantern. The business name does not have a logo design.

We would like a website that is light in colours and creates a warm atmosphere. The design needs to be elegant and upmarket. There are different size candles that we hire out, ranging from 10cm diameter to 20cm diameter, flat, tall etc. All our candles are white in colour. Its just the size that differs.

We would also like to include a section for hiring out decor such as glassvases, candlebras, overlays and chairs sachets, chair covers. However, this is not the businesses main focus but an additional offering to customers.

Target Market(s)

Wedding venues and brides. Corporate events. School dances.

Industry/Entity Type

Hospitality

Logo Text

Hire a Lantern

Number of Pages Required

1 page

Font styles to use
Sans Serif
Script

Requirements
Must have
• Pictures of pillar candles. Plain white candles. The website must centre around candles.
Nice to have
• Different examples of candle centrepieces
Should not have
• Pictures must not be of brides. Pictures of surrounding is perferable.

```html
<!DOCTYPE html>
<html lang="en">
<head>
<meta charset="utf-8">
<title>Hire a Lantern</title>
<link href="https://fonts.googleapis.com/css2?family=Questrial&family=Lato:wght@400;700&family=Pacifico&display=swap" rel="stylesheet">
<style>
:root{
  --orange:#f07c1b;
  --yellow:#fcb514;
  --ink:#222222;
  --body:#555555;
  --muted:#777777;
  --btn-grey:#5e5e5e;
  --band-grey:#ececec;
  --band-cream:#f5f2e6;
  --footer:#ececec;
  --bar:#333333;
  --white:#ffffff;
  --rule:#d9d9d9;
}
*{box-sizing:border-box;margin:0;padding:0}
html,body{width:1200px;height:2757px;overflow:hidden;background:var(--white)}
body{position:relative;font-family:"Lato",Arial,sans-serif;color:var(--body)}
.heading{font-family:"Questrial",Arial,sans-serif;font-weight:400;color:var(--ink);font-size:42px;text-align:center;position:absolute;left:0;width:1200px}

/* header */
.site-header{position:absolute;left:0;top:0;width:1200px;height:120px;background:var(--white)}
.brand{position:absolute;left:81px;top:56px;display:flex;align-items:center;gap:14px}
.brand-mark{width:26px;height:26px;border-radius:50%;background:var(--orange)}
.brand-name{font-family:"Questrial",Arial,sans-serif;font-size:38px;color:var(--ink);line-height:1}
.account{position:absolute;top:24px;right:84px;display:flex;gap:34px;font-size:13px;color:var(--muted)}
.account span{display:flex;align-items:center;gap:7px}
.account svg{width:14px;height:14px}
.main-nav{position:absolute;top:68px;left:674px;display:flex;font-family:"Questrial",Arial,sans-serif;font-size:16px;color:var(--ink)}
.main-nav a{color:inherit;text-decoration:none;padding:4px 6px;margin-right:38px}
.main-nav a.active{color:var(--orange);border:1px solid var(--orange)}
.main-nav a:last-child{margin-right:0}

/* hero */
.hero{position:absolute;left:0;top:120px;width:1200px;height:532px;overflow:hidden}
.hero-photo-left{position:absolute;left:0;top:0;width:590px;height:532px;background:radial-gradient(ellipse at 48% 45%,#f3cf86 0%,#8a7a3c 28%,#3d4a22 50%,#6b5a4a 75%,#c7b9ad 100%)}
.hero-photo-right{position:absolute;left:590px;top:0;width:610px;height:532px;background:radial-gradient(ellipse at 50% 50%,#f7f3e3 0%,#e4e0c4 40%,#b9c47a 70%,#8c8f6a 100%)}
.hero-badge{position:absolute;left:445px;top:143px;width:312px;height:312px;border-radius:50%;background:rgba(255,255,255,.94);text-align:center;padding-top:78px}
.hero-badge .lead{font-family:"Questrial",Arial,sans-serif;font-size:22px;letter-spacing:1px;line-height:36px;color:#333}
.hero-badge .script{font-family:"Pacifico",cursive;font-size:34px;line-height:42px;color:var(--orange);margin-top:8px}
.hero-arrow{position:absolute;top:236px;width:30px;height:60px}
.hero-arrow.prev{left:26px}
.hero-arrow.next{right:26px}

/* about */
.about-title{top:696px}
.about-copy{position:absolute;left:84px;top:762px;width:1032px;text-align:center;font-size:13.5px;line-height:25px;color:var(--body)}
.btn{display:inline-block;font-family:"Lato",Arial,sans-serif;font-size:15px;color:var(--white);text-align:center}
.btn-read{position:absolute;left:541px;top:858px;width:118px;height:39px;line-height:39px;background:var(--orange)}

/* products */
.products{position:absolute;left:0;top:947px;width:1200px;height:628px;background:var(--band-grey)}
.products .heading{top:46px}
.product-card{position:absolute;top:136px;width:334px;height:448px;background:var(--white)}
.product-photo{position:absolute;left:11px;top:10px;width:312px;height:206px}
.photo-hire{background:linear-gradient(160deg,#c9d69a 0%,#f2efe4 45%,#8fa25c 100%)}
.photo-personal{background:radial-gradient(ellipse at 50% 55%,#d8cfc8 0%,#7e6f68 55%,#4d403b 100%)}
.photo-decor{background:linear-gradient(180deg,#ecebe8 0%,#cfcfcf 50%,#5d7a30 80%,#2c2c2c 100%)}
.product-name{position:absolute;left:11px;top:228px;font-family:"Questrial",Arial,sans-serif;font-weight:700;font-size:23px;color:var(--orange)}
.product-text{position:absolute;left:11px;top:264px;width:282px;font-size:13px;line-height:26px;color:var(--body)}
.btn-buy{position:absolute;left:11px;top:382px;width:118px;height:39px;line-height:39px;background:var(--btn-grey)}
.btn-info{position:absolute;left:140px;top:382px;width:118px;height:39px;line-height:39px;background:var(--yellow);color:#333}

/* how it works */
.how-title{top:1623px}
.step{position:absolute;top:1753px;width:220px;text-align:center}
.step-icon{width:148px;height:148px;border-radius:50%;margin:0 auto;display:flex;align-items:center;justify-content:center}
.step-icon.orange{background:var(--orange)}
.step-icon.yellow{background:var(--yellow)}
.step-icon svg{width:80px;height:80px}
.step-label{margin-top:24px;font-size:21px;line-height:29px;color:#666}
.flow-arrow{position:absolute}

/* decor */
.decor{position:absolute;left:0;top:2031px;width:1200px;height:391px;background:var(--band-cream)}
.decor .heading{top:50px}
.decor-tile{position:absolute;top:152px;width:252px;height:188px;display:flex;align-items:center;justify-content:center;text-align:center}
.decor-tile::after{content:"";position:absolute;left:8px;top:8px;right:8px;bottom:8px;border:1px solid rgba(255,255,255,.8)}
.decor-tile span{position:relative;z-index:1;font-family:"Questrial",Arial,sans-serif;font-weight:700;font-size:23px;line-height:32px;color:var(--white)}
.tile-vases{background:radial-gradient(ellipse at 50% 50%,#a49686 0%,#4a3f38 60%,#1d1a18 100%)}
.tile-bras{background:radial-gradient(ellipse at 50% 50%,#b7a47d 0%,#7b6b4f 60%,#4a3f2e 100%)}
.tile-overlays{background:radial-gradient(ellipse at 50% 45%,#b8b1ac 0%,#5e5956 55%,#2a2827 100%)}
.tile-covers{background:radial-gradient(ellipse at 50% 50%,#e2b9c2 0%,#9b7b84 55%,#3f3437 100%)}

/* footer */
.site-footer{position:absolute;left:0;top:2422px;width:1200px;height:285px;background:var(--footer)}
.foot-col{position:absolute;top:36px}
.foot-col h4{font-family:"Lato",Arial,sans-serif;font-weight:400;font-size:15px;color:#333;margin-bottom:22px}
.quick-links{list-style:none;font-size:12.5px;color:#555}
.quick-links li{position:relative;padding-left:18px;margin-bottom:20px}
.quick-links li::before{content:"";position:absolute;left:2px;top:5px;width:6px;height:6px;border:1px solid #777;border-radius:50%}
.contact-row{display:flex;gap:12px;font-size:12.5px;line-height:18px;color:#555;margin-bottom:18px}
.contact-row svg{flex:0 0 20px;width:20px;height:20px}
.field{width:240px;height:32px;border:1px solid #8a8a8a;background:var(--white);font-size:12px;color:#666;padding:6px 10px;margin-bottom:7px}
.field.tall{height:76px}
.btn-submit{width:240px;height:32px;line-height:32px;background:var(--orange);font-size:14px}
.social-row{display:flex;align-items:center;gap:14px;margin-bottom:10px;font-size:12.5px;color:#4a7fc1}
.social-dot{width:32px;height:32px;border-radius:50%;background:#9a9a9a}
.bottom-bar{position:absolute;left:0;top:2707px;width:1200px;height:50px;background:var(--bar);color:#e6e6e6;font-size:14px}
.bottom-bar .copy{position:absolute;left:81px;top:16px}
.bottom-bar .accept{position:absolute;left:912px;top:14px;display:flex;align-items:center;gap:6px}
.card-chip{width:30px;height:20px;background:#f2f2f2;border-radius:2px}
</style>
</head>
<body>

<header class="site-header">
  <div class="brand"><span class="brand-mark"></span><span class="brand-name">Hire a Lantern</span></div>
  <div class="account">
    <span><svg viewBox="0 0 14 14"><rect x="4" y="1" width="9" height="12" fill="none" stroke="#777"/><path d="M1 7h7M6 5l2 2-2 2" fill="none" stroke="#777"/></svg>log in</span>
    <span><svg viewBox="0 0 14 14"><rect x="1" y="2" width="12" height="10" fill="none" stroke="#777"/><path d="M3 5h8M3 8h6" stroke="#777"/></svg>Register</span>
  </div>
  <nav class="main-nav">
    <a class="active" href="#">Home</a>
    <a href="#">About Us</a>
    <a href="#">Our Products</a>
    <a href="#">Contact Us</a>
  </nav>
</header>

<section class="hero">
  <div class="hero-photo-left" role="img" aria-label="Table centrepiece of white roses and greenery around a glass-hurricane pillar candle"></div>
  <div class="hero-photo-right" role="img" aria-label="Set reception table with white pillar candles, wine glasses and green tulips"></div>
  <div class="hero-badge">
    <div class="lead">WE DESIGN,<br>MANUFACTURE<br>&amp; PERSONALISE</div>
    <div class="script">Decorative<br>Candles</div>
  </div>
  <svg class="hero-arrow prev" viewBox="0 0 30 60"><path d="M24 4L6 30l18 26" fill="none" stroke="#fff" stroke-width="3"/></svg>
  <svg class="hero-arrow next" viewBox="0 0 30 60"><path d="M6 4l18 26L6 56" fill="none" stroke="#fff" stroke-width="3"/></svg>
</section>

<h2 class="heading about-title">About Us</h2>
<p class="about-copy">We are a family owned and operated company and began making decorative candles for all occasions. &nbsp;All of our candles are individually hand made in our candle studio, situated in Millbrook, outside Riverton. &nbsp;Our wax is local and of a very high quality, and dripless! Our wax is also made with a high melting point, which means it will not melt or bend in hot temperatures.</p>
<a class="btn btn-read">Read More</a>

<section class="products">
  <h2 class="heading">Our Products</h2>
  <article class="product-card" style="left:79px">
    <div class="product-photo photo-hire" role="img" aria-label="Large white pillar candle surrounded by white roses outdoors"></div>
    <h3 class="product-name">Hire Candles</h3>
    <p class="product-text">Do you love using candles for your events but tired of sorting old used candles or buying expensive candles. Believe it or not you can now rent candles.</p>
    <a class="btn btn-buy">Buy Now</a><a class="btn btn-info">More Info</a>
  </article>
  <article class="product-card" style="left:433px">
    <div class="product-photo photo-personal" role="img" aria-label="Two white floating candles in stemmed glass bowls"></div>
    <h3 class="product-name">Personalised Candles</h3>
    <p class="product-text">Do you love using candles for your events but tired of sorting old used candles or buying expensive candles. Believe it or not you can now rent candles.</p>
    <a class="btn btn-buy">Buy Now</a><a class="btn btn-info">More Info</a>
  </article>
  <article class="product-card" style="left:787px">
    <div class="product-photo photo-decor" role="img" aria-label="Group of green and black pillar candles around a silver candlestick"></div>
    <h3 class="product-name">Décor Hire</h3>
    <p class="product-text">Do you love using candles for your events but tired of sorting old used candles or buying expensive candles. Believe it or not you can now rent candles.</p>
    <a class="btn btn-buy">Buy Now</a><a class="btn btn-info">More Info</a>
  </article>
</section>

<h2 class="heading how-title">How It Works</h2>

<svg class="flow-arrow" style="left:250px;top:1718px" width="110" height="40" viewBox="0 0 110 40"><path d="M4 30Q50 4 100 18" fill="none" stroke="#d6d6d6" stroke-width="2.5"/><path d="M88 8l14 10-16 6" fill="none" stroke="#d6d6d6" stroke-width="2.5"/></svg>
<svg class="flow-arrow" style="left:545px;top:1890px" width="110" height="40" viewBox="0 0 110 40"><path d="M4 24Q52 40 100 12" fill="none" stroke="#d6d6d6" stroke-width="2.5"/><path d="M86 8l16 4-8 14" fill="none" stroke="#d6d6d6" stroke-width="2.5"/></svg>
<svg class="flow-arrow" style="left:840px;top:1718px" width="110" height="40" viewBox="0 0 110 40"><path d="M4 30Q50 4 100 18" fill="none" stroke="#d6d6d6" stroke-width="2.5"/><path d="M88 8l14 10-16 6" fill="none" stroke="#d6d6d6" stroke-width="2.5"/></svg>

<div class="step" style="left:44px">
  <div class="step-icon orange"><svg viewBox="0 0 80 80"><path d="M40 6c5 7 5 12 0 16-5-4-5-9 0-16z" fill="#fff"/><rect x="28" y="26" width="24" height="48" rx="3" fill="#fff"/><path d="M28 40h24M28 56h24" stroke="#f07c1b" stroke-width="3"/></svg></div>
  <div class="step-label">Choose your<br>Candle</div>
</div>
<div class="step" style="left:340px">
  <div class="step-icon yellow"><svg viewBox="0 0 80 80"><path d="M30 8a5 5 0 0 1 10 0v28h4V28a5 5 0 0 1 10 0v10a5 5 0 0 1 10 0v22c0 10-8 16-18 16H42c-8 0-13-4-17-11l-9-17a5 5 0 0 1 9-5l5 8z" fill="#fff"/></svg></div>
  <div class="step-label">Book your<br>Candle</div>
</div>
<div class="step" style="left:640px">
  <div class="step-icon orange"><svg viewBox="0 0 80 80"><rect x="8" y="24" width="64" height="36" rx="3" fill="#fff" transform="rotate(-12 40 42)"/><circle cx="40" cy="42" r="9" fill="#f07c1b"/><rect x="16" y="32" width="48" height="20" fill="none" stroke="#f07c1b" stroke-width="2" transform="rotate(-12 40 42)"/></svg></div>
  <div class="step-label">Make<br>payment</div>
</div>
<div class="step" style="left:934px">
  <div class="step-icon yellow"><svg viewBox="0 0 80 80"><path d="M40 6c5 7 5 12 0 16-5-4-5-9 0-16z" fill="#fff"/><rect x="30" y="26" width="20" height="38" rx="2" fill="#fff"/><path d="M14 64h52l-6 8H20z" fill="#fff"/></svg></div>
  <div class="step-label" style="margin-top:16px">Light Up<br>Your Event</div>
</div>

<section class="decor">
  <h2 class="heading">Our Hiring Out Decor</h2>
  <div class="decor-tile tile-vases" style="left:81px" role="img" aria-label="Glass vases holding lit white pillar candles"><span>Glass Vases</span></div>
  <div class="decor-tile tile-bras" style="left:342px" role="img" aria-label="Glass candelabras with candles on a table"><span>Candle Bras</span></div>
  <div class="decor-tile tile-overlays" style="left:605px" role="img" aria-label="Lace overlay and chair sash tied on a chair"><span>Overlays &amp;<br>Chairs Sachets</span></div>
  <div class="decor-tile tile-covers" style="left:866px" role="img" aria-label="Row of chair covers with pink sashes"><span>Chair Covers</span></div>
</section>

<footer class="site-footer">
  <div class="foot-col" style="left:81px">
    <h4>Quick Links</h4>
    <ul class="quick-links"><li>Home</li><li>About Us</li><li>Our Products</li><li>Contact Us</li></ul>
  </div>
  <div class="foot-col" style="left:303px">
    <h4>Contact Details</h4>
    <div class="contact-row"><svg viewBox="0 0 20 20"><path d="M10 2a6 6 0 0 1 6 6c0 5-6 10-6 10S4 13 4 8a6 6 0 0 1 6-6z" fill="none" stroke="#777" stroke-width="1.5"/><circle cx="10" cy="8" r="2" fill="#777"/></svg><span>1/23 Lorem Ips Dolo, Consecer<br>wererr Nonuy - 12345</span></div>
    <div class="contact-row"><svg viewBox="0 0 20 20"><path d="M5 2h3l1 4-2 2c1 2 3 4 5 5l2-2 4 1v3c0 1-1 2-2 2C9 17 3 11 3 4c0-1 1-2 2-2z" fill="none" stroke="#777" stroke-width="1.5"/></svg><span style="font-size:14px">123-456-7890</span></div>
    <div class="contact-row"><svg viewBox="0 0 20 20"><rect x="2" y="5" width="16" height="11" fill="none" stroke="#777" stroke-width="1.5"/><path d="M2 5l8 6 8-6" fill="none" stroke="#777" stroke-width="1.5"/></svg><span style="font-size:14px">info@companyname.com</span></div>
  </div>
  <div class="foot-col" style="left:651px">
    <h4>Quick Inquiry</h4>
    <div class="field">Name</div>
    <div class="field">Phone</div>
    <div class="field tall">Message</div>
    <a class="btn btn-submit">Submit</a>
  </div>
  <div class="foot-col" style="left:1002px">
    <h4>Follow Us</h4>
    <div class="social-row"><span class="social-dot"></span>Friendhub</div>
    <div class="social-row"><span class="social-dot"></span>Chirpline</div>
    <div class="social-row"><span class="social-dot"></span>WorkLink</div>
    <div class="social-row" style="color:#d24a3a"><span class="social-dot"></span>CirclePlus</div>
  </div>
</footer>

<div class="bottom-bar">
  <div class="copy">Copyright © 2016 Hire a Lantern. All Rights Reserved.</div>
  <div class="accept">We Accept: &nbsp;<span class="card-chip"></span><span class="card-chip"></span><span class="card-chip"></span><span class="card-chip"></span></div>
</div>

</body>
</html>
```